Business Card and Letterhead for Pimlu - modern real estate business

I need a double sided business card design for Pimlu. Please see business card brief here https://files.trelvonadocs.com/sheet/r/7QzTmWbaXLJnoPEd-kRyUgFhHsstbvCe2qfoMxDa_pz/view?mode=shared

Please feel free to design the business cards however you feel best. I am happy to give some creative freedoms and then provide feedback from there.

Please then also create a letterhead to match the business card design

Colors

Designer to choose colors to be used in the design.

Requirements
Must have
• Must be a modern, elegant business card which looks very professional

```html
<!DOCTYPE html>
<html lang="en">
<head>
<meta charset="utf-8">
<title>Pimlu – Business Card</title>
<link rel="stylesheet" href="https://fonts.googleapis.com/css2?family=Montserrat:wght@400;500;600;700&display=swap">
<style>
  :root {
    --page: #ecebe9;
    --card: #2e2e30;
    --card-edge: #1f1f21;
    --red: #e3141c;
    --white: #ffffff;
    --rule: #c9c9c9;
    --photo-top: #8d8d8f;
    --photo-bottom: #3a3a3d;
  }
  * { box-sizing: border-box; margin: 0; padding: 0; }
  html, body { width: 1200px; height: 800px; overflow: hidden; }
  body {
    background: var(--page);
    font-family: "Montserrat", sans-serif;
    position: relative;
  }
  .card {
    position: absolute;
    top: 245px;
    width: 525px;
    height: 300px;
    background: var(--card);
    overflow: hidden;
    box-shadow: 0 6px 18px rgba(0,0,0,0.18);
  }
  .card--front { left: 50px; }
  .card--back { left: 625px; }

  /* Front */
  .brand-name {
    position: absolute;
    left: 0; right: 0;
    top: 110px;
    text-align: center;
    color: var(--red);
    font-weight: 600;
    font-size: 64px;
    letter-spacing: 6px;
    line-height: 1;
  }
  .front-stripe {
    position: absolute;
    left: 0; right: 0; bottom: 0;
    height: 8px;
    background: var(--red);
  }

  /* Back */
  .agent-photo {
    position: absolute;
    left: 0; bottom: 0;
    width: 245px;
    height: 268px;
    background: linear-gradient(180deg, var(--photo-top), var(--photo-bottom));
  }
  .back-stripe {
    position: absolute;
    left: 245px; right: 0; bottom: 0;
    height: 8px;
    background: var(--red);
  }
  .agent-details {
    position: absolute;
    left: 260px; right: 18px;
    top: 52px;
    text-align: right;
    color: var(--white);
  }
  .agent-name {
    color: var(--red);
    font-weight: 600;
    font-size: 24px;
    letter-spacing: 2.5px;
    text-transform: uppercase;
    line-height: 1.1;
  }
  .agent-title {
    font-size: 14px;
    font-weight: 500;
    margin-top: 2px;
    letter-spacing: 0.3px;
  }
  .contact-icons {
    display: flex;
    align-items: center;
    justify-content: center;
    gap: 6px;
    margin: 18px 0 6px 30px;
    width: 170px;
  }
  .contact-icons .rule { flex: 1; height: 1px; background: var(--rule); }
  .contact-list {
    list-style: none;
    width: 170px;
    margin-left: 30px;
    text-align: center;
    font-size: 13.5px;
    line-height: 1.35;
  }
  .divider {
    width: 150px;
    height: 1px;
    background: var(--rule);
    margin: 10px 0 10px 40px;
  }
  .address {
    width: 170px;
    margin-left: 30px;
    text-align: center;
    font-size: 13.5px;
    line-height: 1.35;
    font-style: normal;
  }
</style>
</head>
<body>

<section class="card card--front" aria-label="Business card front">
  <div class="brand-name">PIMLU</div>
  <div class="front-stripe"></div>
</section>

<section class="card card--back" aria-label="Business card back">
  <div class="agent-photo" role="img" aria-label="Portrait photo of the agent in a dark suit"></div>
  <div class="back-stripe"></div>

  <div class="agent-details">
    <h1 class="agent-name">Dane Morrow</h1>
    <p class="agent-title">Licenced Real Estate Agent</p>

    <div class="contact-icons">
      <span class="rule"></span>
      <svg width="16" height="16" viewBox="0 0 16 16" aria-label="Phone">
        <circle cx="8" cy="8" r="8" fill="var(--red)"/>
        <path d="M5.2 4.2l1.4-.3.8 1.8-.9.7c.4.9 1.2 1.7 2.1 2.1l.7-.9 1.8.8-.3 1.4c-3 .3-6-2.7-5.6-5.6z" fill="var(--white)"/>
      </svg>
      <svg width="16" height="16" viewBox="0 0 16 16" aria-label="Email">
        <circle cx="8" cy="8" r="8" fill="var(--red)"/>
        <rect x="4" y="5.2" width="8" height="5.6" fill="var(--white)"/>
        <path d="M4 5.2l4 3 4-3" fill="none" stroke="var(--red)" stroke-width="0.9"/>
      </svg>
      <svg width="16" height="16" viewBox="0 0 16 16" aria-label="Website">
        <circle cx="8" cy="8" r="8" fill="var(--red)"/>
        <circle cx="8" cy="8" r="4" fill="none" stroke="var(--white)" stroke-width="1"/>
        <path d="M4 8h8M8 4c-1.6 2.4-1.6 5.6 0 8M8 4c1.6 2.4 1.6 5.6 0 8" fill="none" stroke="var(--white)" stroke-width="0.8"/>
      </svg>
      <span class="rule"></span>
    </div>

    <ul class="contact-list">
      <li>0400 318 529</li>
      <li>dane@pimlu.com</li>
      <li>www.pimlu.com</li>
    </ul>

    <div class="divider"></div>

    <address class="address">
      PO Box 7160<br>
      Corrindale NSW 2790
    </address>
  </div>
</section>

</body>
</html>
```